Business cards and stationary design

We just completed the design of our new logo and we need to print new business cards and letterhead for our nonprofit. We are looking for a fresh new design that shows off our new logo. On letterhead, we must have a column on the right or left to include our Board of Directors (up to 45 names) (see attachment)

Industry/Entity Type

Non-Profit

Contact Information for Business Card

Standard business card with name, title, Company name, mailing address phone numbers, email address and website. Tagline on back "Bringing the homeless home"

Font styles to use
Sans Serif

Requirements
Must have
• include pertinent information above
• new logo
• fonts compatible with logo
• should use logo colors only
Nice to have
• tag lines

```html
<!DOCTYPE html>
<html lang="en">
<head>
<meta charset="utf-8">
<title>Homeward Haven Center – Business Card</title>
<link rel="stylesheet" href="https://fonts.googleapis.com/css2?family=Michroma&family=Nunito+Sans:wght@400;600&display=swap">
<style>
  :root {
    --backdrop: #e4e4e4;
    --card-white: #f8f8f8;
    --teal: #0483a4;
    --sunshine: #f7b924;
    --crimson: #d62027;
    --white: #ffffff;
    --card-shadow: 0 3px 6px rgba(0,0,0,0.35);
  }
  * { box-sizing: border-box; margin: 0; padding: 0; }
  html, body {
    width: 1200px; height: 582px; overflow: hidden;
    background: var(--backdrop);
  }
  .stage { position: relative; width: 1200px; height: 582px; }
  .card {
    position: absolute; top: 158px;
    width: 464px; height: 264px;
    box-shadow: var(--card-shadow);
    overflow: hidden;
  }
  .card-front { left: 122px; background: var(--card-white); }
  .card-back { left: 602px; background: var(--crimson); }

  .front-band { position: absolute; inset: 0; width: 464px; height: 264px; }

  .org-name {
    position: absolute; left: 24px; top: 58px; width: 200px;
    font-family: "Michroma", sans-serif; font-size: 13px; line-height: 19px;
    color: var(--teal); text-align: center; letter-spacing: 1px;
  }
  .org-mark {
    display: block; width: 14px; height: 14px; margin: 0 auto 10px;
    background: var(--teal);
  }

  .contact {
    position: absolute; right: 26px; top: 112px;
    text-align: right; color: var(--white);
    font-family: "Nunito Sans", sans-serif;
  }
  .person-name {
    font-family: "Michroma", sans-serif; font-size: 15px; letter-spacing: 1px; line-height: 18px;
  }
  .person-title {
    font-family: "Michroma", sans-serif; font-size: 8.5px; letter-spacing: 1.5px; margin-bottom: 8px;
  }
  .address { font-size: 10.5px; line-height: 13.5px; margin-bottom: 8px; }
  .channel { font-size: 10.5px; line-height: 15px; display: flex; justify-content: flex-end; align-items: center; gap: 6px; }
  .channel-phone { font-size: 12px; }
  .channel svg { width: 10px; height: 10px; fill: var(--white); }

  .back-name {
    position: absolute; left: 0; right: 0; top: 100px;
    text-align: center; color: var(--white);
    font-family: "Michroma", sans-serif; font-size: 20px; letter-spacing: 2px;
  }
  .back-web {
    position: absolute; left: 0; right: 0; top: 224px;
    text-align: center; color: var(--white);
    font-family: "Michroma", sans-serif; font-size: 9px; letter-spacing: 3.5px;
  }
</style>
</head>
<body>
<main class="stage">
  <section class="card card-front">
    <svg class="front-band" viewBox="0 0 464 264" aria-hidden="true">
      <polygon points="0,238 464,18 464,32 0,252" fill="var(--sunshine)"/>
      <polygon points="0,252 464,32 464,264 0,264" fill="var(--teal)"/>
    </svg>
    <div class="org-name"><span class="org-mark"></span>HOMEWARD HAVEN<br>CENTER</div>
    <div class="contact">
      <p class="person-name">DANIEL REYES</p>
      <p class="person-title">CEO/FOUNDER</p>
      <p class="address">Homeward haven center<br>1420 Birchwood Avenue<br>Fairbanks, Alaska 99701</p>
      <p class="channel channel-phone">555 214 7391
        <svg viewBox="0 0 24 24"><path d="M6.6 10.8a15.2 15.2 0 0 0 6.6 6.6l2.2-2.2c.3-.3.7-.4 1-.2 1.1.4 2.3.6 3.6.6.6 0 1 .4 1 1V20c0 .6-.4 1-1 1A17 17 0 0 1 3 4c0-.6.4-1 1-1h3.5c.6 0 1 .4 1 1 0 1.3.2 2.5.6 3.6.1.3 0 .7-.2 1z"/></svg>
      </p>
      <p class="channel">daniel@homewardhaven.org
        <svg viewBox="0 0 24 24"><path d="M2 5h20v14H2zm2 2v.5l8 5 8-5V7l-8 5z"/></svg>
      </p>
      <p class="channel">www.homewardhaven.org
        <svg viewBox="0 0 24 24"><circle cx="12" cy="12" r="10"/></svg>
      </p>
    </div>
  </section>

  <section class="card card-back">
    <p class="back-name">HOMEWARD HAVEN</p>
    <p class="back-web">WWW.HOMEWARDHAVEN.ORG</p>
  </section>
</main>
</body>
</html>
```